Software Platform User Guide (Manual)

We need a user manual template for our online e-learning platform, Lanthorn, which allows users to create their own online courses.

We’re looking for a template for a few pages, including a cover, back page, table of contents, and pages for text-only (or bullet points), and text & images (screenshots). We would like to be able to add new pages and adjust textual content ourselves. Lorem ipsum is totally cool as placeholder text. The name of the product is Lanthorn, but the company name is Cordwain Meridian, so we would like the cover and back cover to say “Cordwain Meridian" and "Lanthorn".

We have uploaded a few files to give you a sense of our color scheme and logo. You can also check out our website at cmvista.example for an idea of our aesthetic sensibility. The design should be simple and elegant, and (being a user manual) clarity is king. We use Avenir and Elizabeth as or primary fonts. We have also uploaded some sample screen shots from Lanthorn. You can use those screenshots to help direct your work, but note that the interface design is changing soon; i.e., you should emphasize the Cordwain Meridian brand aesthetic more so than the Lanthorn user interface design.

Target Market(s)

Businesses and nonprofits looking to implement our platform. Many buyers are female, but the people reading the manual are typically male.

Industry/Entity Type

It Company

Requirements
Must have
• The final product must be a template that will work in Microsoft Word, PowerPoint, or Apple Keynote/Pages. It's fine to send PDFs for previews. Note we need the final product in ONE of the above choices (Word, Powerpoint, Keynote, or Pages), not ALL.

You must make use of the CM logo and fonts on every page. Note that the tag line, "quickest bridge across two shores of thought" in one version of the logo does note have to be included.

We need clear delineation between headers, sub-headers, and bullets, as well as a great looking cover, table of contents and back page.

Please Note: Please disregard the OLUD logo on any screenshots. These were mockups for a client. Please don't use the OLUD name or logo.

```html
<!DOCTYPE html>
<html lang="en">
<head>
<meta charset="utf-8">
<title>Lanthorn User Manual – Cover Set</title>
<link rel="stylesheet" href="https://fonts.googleapis.com/css2?family=Nunito+Sans:wght@300;400&family=Playfair+Display:wght@400;500&display=swap">
<style>
  :root {
    --page-bg: #ababab;
    --panel-light: #8d8d8d;
    --panel-dark: #575757;
    --lime: #b3ff00;
    --ring: #2a2a2a;
    --title-grey: #6a6a6a;
    --accent-blue: #4b9deb;
    --white: #ffffff;
    --trim: #6f6f6f;
  }
  html, body {
    margin: 0;
    width: 1200px;
    height: 900px;
    overflow: hidden;
    background: var(--page-bg);
  }
  .sheet {
    position: relative;
    width: 1200px;
    height: 900px;
    background: var(--page-bg);
  }
  .trim-line {
    position: absolute;
    left: 22px; top: 4px;
    width: 1151px; height: 889px;
    border: 1px dashed var(--trim);
    box-sizing: border-box;
  }
  .panel {
    position: absolute;
    top: 25px;
    width: 348px;
    height: 853px;
    border-radius: 14px;
    background: var(--panel-light);
    overflow: hidden;
  }
  .panel--back { left: 44px; }
  .panel--spine { left: 428px; background: var(--panel-dark); }
  .panel--front { left: 809px; }

  .dot-field {
    position: absolute;
    left: 12px; top: 10px;
    width: 324px; height: 500px;
    border-radius: 12px;
  }
  .panel--back .dot-field { background: radial-gradient(ellipse 60% 45% at 50% 22%, rgba(80,80,80,.28), rgba(190,190,190,.1) 65%, rgba(0,0,0,0) 100%); }
  .panel--spine .dot-field { background: radial-gradient(ellipse 60% 45% at 50% 22%, rgba(220,220,220,.16), rgba(160,160,160,.06) 65%, rgba(0,0,0,0) 100%); }
  .panel--front .dot-field { background: radial-gradient(ellipse 60% 45% at 50% 22%, rgba(179,255,0,.24), rgba(179,255,0,.08) 65%, rgba(0,0,0,0) 100%); }

  .dot-rule {
    position: absolute;
    left: 18px; top: 583px;
    width: 312px; height: 6px;
    border-radius: 3px;
    background: linear-gradient(90deg, rgba(200,200,200,.15), rgba(255,255,255,.85) 50%, rgba(200,200,200,.15));
  }

  .cover-disc {
    position: absolute;
    left: 12px; top: 150px;
    width: 324px; height: 324px;
    border-radius: 50%;
    background: var(--lime);
    border: 1px solid var(--ring);
    box-sizing: border-box;
    display: flex;
    flex-direction: column;
    align-items: center;
    justify-content: center;
    padding-top: 26px;
  }
  .product-name {
    font-family: "Nunito Sans", sans-serif;
    font-weight: 300;
    font-size: 49px;
    line-height: 1;
    color: var(--title-grey);
    letter-spacing: 0.5px;
  }
  .panel--back .product-name { color: var(--white); }
  .doc-type {
    font-family: "Playfair Display", serif;
    font-size: 22px;
    line-height: 1;
    margin-top: 4px;
    color: var(--accent-blue);
  }

  .company-line {
    position: absolute;
    left: 0; right: 0; top: 500px;
    margin: 0;
    text-align: center;
    font-family: "Playfair Display", serif;
    font-size: 23px;
    line-height: 30px;
    letter-spacing: 3.4px;
    color: var(--white);
  }

  .badge-disc {
    position: absolute;
    top: 718px;
    width: 98px; height: 98px;
    border-radius: 50%;
    background: var(--lime);
    border: 1px solid var(--ring);
    box-sizing: border-box;
    display: flex;
    align-items: center;
    justify-content: center;
    font-family: "Nunito Sans", sans-serif;
    font-weight: 400;
    font-size: 14px;
    color: var(--white);
  }
  .panel--back .badge-disc { left: 17px; }
  .panel--front .badge-disc { left: 231px; }

  .brand-name {
    position: absolute;
    left: 0; right: 0; top: 738px;
    text-align: center;
    font-family: "Playfair Display", serif;
    font-size: 64px;
    line-height: 1;
    color: var(--white);
  }

  .contact-block {
    position: absolute;
    left: 49px; top: 612px;
    margin: 0;
    font-family: "Playfair Display", serif;
    font-style: normal;
    font-weight: 500;
    font-variant-numeric: lining-nums;
    font-size: 18px;
    line-height: 24px;
    color: var(--white);
  }
</style>
</head>
<body>
<main class="sheet">
  <div class="trim-line"></div>

  <section class="panel panel--back">
    <div class="dot-field" role="img" aria-label="Soft grey dot grid pattern"></div>
    <div class="cover-disc">
      <span class="product-name">Lanthorn</span>
      <span class="doc-type">user manual</span>
    </div>
    <p class="company-line">cordwain meridian</p>
    <div class="dot-rule" role="img" aria-label="Row of dots fading out from the centre"></div>
    <div class="badge-disc">Lanthorn</div>
  </section>

  <section class="panel panel--spine">
    <div class="dot-field" role="img" aria-label="Light dot grid pattern on dark grey"></div>
    <div class="cover-disc">
      <span class="product-name">Lanthorn</span>
      <span class="doc-type">user manual</span>
    </div>
    <div class="dot-rule" role="img" aria-label="Row of dots fading out from the centre"></div>
    <div class="brand-name">cm</div>
  </section>

  <section class="panel panel--front">
    <div class="dot-field" role="img" aria-label="Lime green dot grid pattern"></div>
    <div class="cover-disc">
      <span class="product-name">Lanthorn</span>
      <span class="doc-type">user manual</span>
    </div>
    <p class="company-line">cordwain meridian</p>
    <div class="dot-rule" role="img" aria-label="Row of dots fading out from the centre"></div>
    <address class="contact-block">
      Cordwain Meridian, LLC.<br>
      27 Harrow Lane<br>
      Brightwater, Vermont 05099<br>
      +1 555-014-2290
    </address>
    <div class="badge-disc">Lanthorn</div>
  </section>
</main>
</body>
</html>
```